Food and Beverage Business Cards

We need business cards with logo designs for a consultant in the food and beverage industry. We specialize in helping restaurants fix operational and management problems.
Specific areas of expertise include:
-Steps of service
-Staff management tools
-Standard operating procedures
-Profit and loss management
-Inventory
-Point of sales
-Bar Menu
-Mystery shopper service
-Handling and managing suppliers

Target Market(s)

Restaurant and bar owners and managers

Industry/Entity Type

Business

Contact Information for Business Card

Mathieu Girardot
Q&T Consulting
phone: 15027390614
mathqt@sampleinbox.com

Font styles to use
Other font styles liked:
• Check out the screen shot font idea

Colors

Designer to choose colors to be used in the design.

Requirements
Must have
• Must include QR code (See attachment)
• Logo should reflect our specific focus on the drinks side of the industry.
• Areas of Expertise:
• -Service Steps
• -Staff management tools
• -S.O.P
• -P&L Management
• -Inventory
• -P.O.S
• -Bar Menu
• -Mystery Shopper Service
• -Handling and Managing Suppliers

```html
<!DOCTYPE html>
<html lang="en">
<head>
<meta charset="utf-8">
<title>Q&amp;T Consulting – Business Cards</title>
<link rel="stylesheet" href="https://fonts.googleapis.com/css2?family=Roboto+Condensed:wght@400;700&display=swap">
<style>
  :root {
    --page-bg: #e9e6e1;
    --card-white: #f4f4f4;
    --card-black: #141414;
    --ink-dark: #1b1b1b;
    --ink-light: #f5f5f5;
    --ink-muted: #d6d6d6;
    --curve-grey: #9a9a9a;
    --badge-fill: #e8e8e8;
    --badge-ring: #bdbdbd;
  }
  * { box-sizing: border-box; margin: 0; padding: 0; }
  html, body {
    width: 1200px; height: 911px; overflow: hidden;
    background: var(--page-bg);
    font-family: "Roboto Condensed", Arial, sans-serif;
  }
  .sheet {
    width: 1200px; height: 911px;
    display: flex; flex-direction: column;
    align-items: center; justify-content: center; gap: 48px;
  }
  .card {
    position: relative; width: 680px; height: 389px;
    border-radius: 22px; overflow: hidden;
    box-shadow: 0 10px 30px rgba(0,0,0,.25);
  }

  /* Brand name */
  .brand-name {
    position: absolute; left: 0; right: 0;
    text-align: center; font-size: 62px; font-weight: 700; line-height: 1;
    white-space: nowrap;
  }

  /* Front */
  .card-front { background: var(--card-white); }
  .front-band { position: absolute; inset: 0; width: 100%; height: 100%; }
  .card-front .brand-name { top: 82px; color: var(--ink-dark); }

  .front-details {
    position: absolute; left: 0; right: 0; bottom: 34px;
    display: flex; align-items: center; justify-content: center; gap: 26px;
    color: var(--ink-light);
  }
  .person { text-align: right; }
  .person-name { font-size: 25px; font-weight: 700; }
  .person-role { font-size: 17px; font-weight: 400; color: var(--ink-muted); margin-top: 2px; }
  .divider { width: 1px; height: 58px; background: var(--ink-muted); }
  .contact-list { list-style: none; font-size: 16px; }
  .contact-list li { display: flex; align-items: center; gap: 9px; margin: 4px 0; }
  .contact-icon { width: 13px; height: 13px; flex: none; }

  /* Back */
  .card-back { background: var(--card-black); color: var(--ink-light); }
  .card-back .brand-name { top: 66px; right: 140px; left: 0; color: var(--ink-light); }
  .badges {
    position: absolute; top: 66px; right: 50px;
    display: flex; gap: 10px; align-items: center;
  }
  .badge {
    width: 40px; height: 40px; border-radius: 50%;
    background: var(--badge-fill); border: 3px solid var(--badge-ring);
  }
  .badge-large { width: 52px; height: 52px; }
  .expertise {
    position: absolute; left: 0; right: 0; top: 196px; text-align: center;
  }
  .expertise-title { font-size: 22px; font-weight: 700; margin-bottom: 14px; }
  .expertise-list { list-style: none; font-size: 17px; line-height: 1.5; color: var(--ink-muted); }
</style>
</head>
<body>
<main class="sheet">

  <section class="card card-front" aria-label="Card front">
    <svg class="front-band" viewBox="0 0 680 389" preserveAspectRatio="none" aria-hidden="true">
      <path d="M0 300 C 200 292, 420 250, 680 168 L680 389 L0 389 Z" fill="#9a9a9a"/>
      <path d="M0 306 C 200 300, 420 260, 680 180 L680 389 L0 389 Z" fill="#141414"/>
    </svg>
    <p class="brand-name">Cellar Row</p>
    <div class="front-details">
      <div class="person">
        <p class="person-name">Mathieu Girardot</p>
        <p class="person-role">Q&amp;T Consulting</p>
      </div>
      <span class="divider"></span>
      <ul class="contact-list">
        <li>
          <svg class="contact-icon" viewBox="0 0 24 24" aria-hidden="true"><path fill="#f5f5f5" d="M6.6 10.8a15.2 15.2 0 0 0 6.6 6.6l2.2-2.2c.3-.3.7-.4 1-.2 1.1.4 2.3.6 3.6.6.6 0 1 .4 1 1V20c0 .6-.4 1-1 1A17 17 0 0 1 3 4c0-.6.4-1 1-1h3.5c.6 0 1 .4 1 1 0 1.3.2 2.5.6 3.6.1.3 0 .7-.2 1z"/></svg>
          <span>15027390614</span>
        </li>
        <li>
          <svg class="contact-icon" viewBox="0 0 24 24" aria-hidden="true"><rect x="2" y="5" width="20" height="14" rx="1" fill="#f5f5f5"/><path d="M3 6l9 7 9-7" fill="none" stroke="#141414" stroke-width="2"/></svg>
          <span>mathqt@sampleinbox.com</span>
        </li>
      </ul>
    </div>
  </section>

  <section class="card card-back" aria-label="Card back">
    <p class="brand-name">Cellar Row</p>
    <div class="badges" aria-hidden="true">
      <span class="badge badge-large"></span>
      <span class="badge"></span>
      <span class="badge"></span>
    </div>
    <div class="expertise">
      <h2 class="expertise-title">Areas of Expertise</h2>
      <ul class="expertise-list">
        <li>Service Steps | Staff management tools | S.O.P | P&amp;L Management</li>
        <li>Inventory | P.O.S | Bar Menu | Mystery Shopper Service</li>
        <li>Handling and Managing Suppliers</li>
      </ul>
    </div>
  </section>

</main>
</body>
</html>
```